New Company Business Card design

Looking for a corporate looking business card utilising my new logo design - the logo i would like embossed as one option and flat as another - simplistic but stylish - less is more - we are an import export business launching into the market - i would like a couple of options as main background - Grey or Black

```html
<!DOCTYPE html>
<html lang="en">
<head>
<meta charset="utf-8">
<title>Meridian Trade Partners — Business Card</title>
<link rel="stylesheet" href="https://fonts.googleapis.com/css2?family=Roboto:wght@400;500&display=swap">
<style>
  :root {
    --page-bg: #e4e5e8;
    --card-white: #ffffff;
    --card-grey: #5d5e62;
    --brand-blue: #1a6fb8;
    --text-grey: #4a4a4e;
    --back-text: #c9cacd;
  }
  * { margin: 0; padding: 0; box-sizing: border-box; }
  html, body { width: 1200px; height: 900px; overflow: hidden; }
  body {
    background: var(--page-bg);
    display: flex;
    flex-direction: column;
    align-items: center;
    justify-content: center;
    gap: 40px;
    font-family: "Roboto", Arial, sans-serif;
  }
  .card {
    width: 700px;
    height: 400px;
    border-radius: 22px;
    position: relative;
    box-shadow: 0 6px 18px rgba(0,0,0,0.15);
    overflow: hidden;
  }
  .card-front {
    background: linear-gradient(135deg, #f1f1f3 0%, var(--card-white) 45%, var(--card-white) 100%);
  }
  .contact-block {
    position: absolute;
    left: 48px;
    top: 70px;
    color: var(--text-grey);
  }
  .person-name {
    color: var(--brand-blue);
    font-weight: 500;
    font-size: 25px;
    letter-spacing: 0.5px;
    text-transform: uppercase;
  }
  .person-role { font-size: 17px; margin-top: 2px; }
  .address { font-size: 17px; line-height: 1.3; margin-top: 16px; }
  .contact-list { list-style: none; margin-top: 16px; font-size: 17px; line-height: 1.45; }
  .contact-list li { display: flex; align-items: center; gap: 10px; }
  .contact-list svg { width: 13px; height: 13px; flex: none; }
  .brand-lockup {
    position: absolute;
    right: 48px;
    top: 50%;
    transform: translateY(-50%);
    display: flex;
    align-items: center;
    gap: 10px;
  }
  .brand-dot { width: 14px; height: 14px; border-radius: 50%; background: var(--brand-blue); flex: none; }
  .brand-name {
    font-family: "Roboto", Arial, sans-serif;
    font-weight: 500;
    font-size: 20px;
    color: var(--brand-blue);
  }
  .card-back {
    background: var(--card-grey);
    display: flex;
    align-items: center;
    justify-content: center;
  }
  .card-back .brand-lockup { position: static; transform: none; gap: 14px; }
  .card-back .brand-dot { background: var(--back-text); width: 20px; height: 20px; }
  .card-back .brand-name { color: var(--back-text); font-size: 32px; }
</style>
</head>
<body>
  <section class="card card-front">
    <div class="contact-block">
      <h1 class="person-name">Adrian Hale</h1>
      <p class="person-role">Director</p>
      <p class="address">2250 Harbor View Ave<br>Marin, CA 94901-3310</p>
      <ul class="contact-list">
        <li><svg viewBox="0 0 16 16"><path fill="var(--brand-blue)" d="M4 1l2.5 3-1.5 1.5c.8 2 2.5 3.7 4.5 4.5L11 8.5l3 2.5-1.5 2.5C7.5 13.5 2.5 8.5 2.5 3z"/></svg>415-555-0182</li>
        <li><svg viewBox="0 0 16 16"><rect x="1.5" y="3.5" width="13" height="9" fill="none" stroke="var(--brand-blue)" stroke-width="1.6"/><path d="M1.5 3.5l6.5 5 6.5-5" fill="none" stroke="var(--brand-blue)" stroke-width="1.6"/></svg>info@meridiantrade.com</li>
        <li><svg viewBox="0 0 16 16"><circle cx="8" cy="8" r="6.5" fill="none" stroke="var(--brand-blue)" stroke-width="1.5"/><ellipse cx="8" cy="8" rx="2.8" ry="6.5" fill="none" stroke="var(--brand-blue)" stroke-width="1.2"/><path d="M1.5 8h13" stroke="var(--brand-blue)" stroke-width="1.2"/></svg>www.meridiantrade.com</li>
      </ul>
    </div>
    <div class="brand-lockup">
      <span class="brand-dot"></span><span class="brand-name">Meridian Trade Partners</span>
    </div>
  </section>

  <section class="card card-back">
    <div class="brand-lockup">
      <span class="brand-dot"></span><span class="brand-name">Meridian Trade Partners</span>
    </div>
  </section>
</body>
</html>
```